HOME PAGE AND AND SECONDARY DESIGN FOR INTERNAL PAGES

Construction company looking for an easy to navagate professional serious greyscale website with a good clean feel simple clean menu and responsive friendly design. Our main clientele is commercial properties business owners and investors of rental properties. This website is going to be static HTML5 and would need multiple sizing files for clean fast rendering. Clean and accurate design files a must so if your experienced awesome modern greyscale designer let's get started I need this done as soon as possible.

Industry/Entity Type

construction, electrical, plumbing, commercial build outs

Number of Pages Required

2 page

Font styles to use
Sans Serif

Colors

Designer to choose only greyscale colors for use in the design.

Requirements
Must have
• Main Menu... Home, Services, Projects, About our team

```html
<!DOCTYPE html>
<html lang="en">
<head>
<meta charset="utf-8">
<title>Ridgeline Build Co. — Home</title>
<link href="https://fonts.googleapis.com/css2?family=Barlow:wght@500;600;700&family=Montserrat:wght@400;500&display=swap" rel="stylesheet">
<style>
:root{
  --white:#ffffff;
  --page:#f2f2f2;
  --panel:#e2e2e2;
  --ink:#2b2b2b;
  --text:#4a4a4a;
  --muted:#6a6a6a;
  --button:#555555;
  --dark:#1b1b1b;
  --ring:#8f8489;
  --team-mid:#5d5d5d;
  --team-side:#d6d6d6;
}
*{box-sizing:border-box;margin:0;padding:0}
html,body{width:1200px;height:3457px;overflow:hidden}
body{background:var(--page);font-family:"Montserrat",sans-serif;color:var(--text);position:relative}
.heading{font-family:"Barlow",sans-serif;font-weight:600;color:var(--ink);text-transform:uppercase}
.btn{position:absolute;background:var(--button);color:var(--white);font-family:"Barlow",sans-serif;font-weight:600;font-size:14px;text-transform:uppercase;display:flex;align-items:center;justify-content:center;white-space:nowrap}

/* header */
.site-header{position:absolute;left:0;top:0;width:1200px;height:91px;background:var(--white);border-bottom:1px solid #dcdcdc}
.brand{position:absolute;left:110px;top:24px;width:140px;text-align:center;font-family:"Barlow",sans-serif;font-weight:600;color:#3a3a3a;font-size:17px;line-height:20px;text-transform:uppercase;letter-spacing:1px}
.main-nav{position:absolute;left:390px;top:35px}
.main-nav a{font-family:"Montserrat",sans-serif;font-weight:500;font-size:15px;color:#3f3f3f;text-decoration:none;position:absolute;white-space:nowrap}

/* hero */
.hero{position:absolute;left:0;top:91px;width:1200px;height:565px;background:linear-gradient(100deg,#4a4a4a 0%,#6e6e6e 45%,#3e3e3e 100%)}
.hero-title{position:absolute;left:162px;top:178px;font-family:"Barlow",sans-serif;font-weight:700;font-size:46px;line-height:47px;color:var(--white)}
.hero-sub{position:absolute;left:162px;top:285px;font-family:"Barlow",sans-serif;font-weight:500;font-size:29px;line-height:39px;color:var(--white)}

/* services */
.section-title{position:absolute;left:0;width:1200px;text-align:center;font-size:33px}
.service-card{position:absolute;top:807px;width:311px;height:367px;background:#fbfbfb;border-top:6px solid var(--button);box-shadow:0 1px 4px rgba(0,0,0,.08)}
.service-icon{position:absolute;left:26px;top:32px;width:80px;height:80px;border-radius:50%;background:#e6e6e6}
.service-card h3{position:absolute;left:29px;top:128px;font-size:20px;line-height:29px;width:270px}
.service-card p{position:absolute;left:29px;top:193px;width:255px;font-size:13.5px;line-height:24px;height:120px;overflow:hidden}
.service-card .btn{left:167px;top:341px;width:144px;height:42px}

/* approach */
.approach-photo{position:absolute;left:0;top:1310px;width:548px;height:586px;background:linear-gradient(160deg,#cfcfcf,#8a8a8a 60%,#5e5e5e)}
.approach-panel{position:absolute;left:569px;top:1310px;width:566px;height:586px;background:var(--panel)}
.approach-panel h2{position:absolute;left:22px;top:16px;font-size:34px;white-space:nowrap}
.approach-panel .lead{position:absolute;left:22px;top:75px;width:500px;font-size:13.5px;line-height:25.7px}
.approach-list{position:absolute;left:40px;top:272px;list-style:none}
.approach-list li{font-size:13.5px;line-height:25.7px;padding-left:22px;position:relative;white-space:nowrap}
.approach-list li::before{content:"";position:absolute;left:0;top:8px;width:10px;height:10px;border-radius:50%;background:#333}
.query-bar{position:absolute;left:40px;top:433px;width:490px;height:43px;background:var(--white);font-family:"Barlow",sans-serif;font-weight:500;font-size:15px;color:#333;padding:12px 14px}
.query-bar svg{position:absolute;right:12px;top:10px}
.approach-panel .btn{left:40px;top:510px;width:138px;height:42px}

/* projects */
.projects{position:absolute;left:0;top:2034px;width:1200px;height:465px;overflow:hidden}
.project{position:absolute;top:0;width:319px;height:465px}
.project .photo{position:absolute;inset:0}
.project h3{position:absolute;left:35px;top:264px;color:var(--white);font-size:23px}
.project p{position:absolute;left:37px;top:298px;width:250px;color:var(--white);font-size:13.5px;line-height:24px}
.project .btn{left:37px;top:387px;width:136px;height:43px;background:#5a5a5a}

/* team */
.team-circle{position:absolute;top:2697px;width:350px;height:350px;border-radius:50%;border:7px solid var(--ring);text-align:center}
.team-circle .avatar{position:absolute;left:96px;top:18px;width:145px;height:145px;border-radius:50%;border:5px solid var(--ring)}
.team-circle h3{position:absolute;left:0;width:336px;top:195px;font-family:"Montserrat",sans-serif;font-weight:500;font-size:15px}
.team-circle p{position:absolute;left:63px;width:210px;top:222px;font-size:12.5px;line-height:19px}
.team-circle svg{position:absolute;left:149px;top:274px}
.team-side{background:var(--team-side);color:#555}
.team-side h3{color:#333}
.team-mid{background:var(--team-mid);color:#e8e8e8;z-index:2}
.team-mid h3{color:var(--white)}

/* footer */
.site-footer{position:absolute;left:0;top:3104px;width:1200px;height:353px;background:var(--dark);color:var(--white)}
.footer-brand{position:absolute;left:130px;top:156px;width:170px;text-align:center;font-family:"Barlow",sans-serif;font-weight:600;font-size:19px;line-height:20px;letter-spacing:1px;text-transform:uppercase}
.footer-col{position:absolute;top:96px}
.footer-col h4{font-family:"Barlow",sans-serif;font-weight:600;font-size:16px;text-decoration:underline;text-underline-offset:3px;margin-bottom:10px}
.footer-col a{display:block;color:var(--white);text-decoration:none;font-size:12px;line-height:25.7px;white-space:nowrap}
.contact-col{width:240px}
.contact-row{position:absolute;left:13px;width:220px;font-size:11.5px;line-height:17px;white-space:nowrap}
.contact-row svg{position:absolute;left:-27px;top:2px}
.footer-rule{position:absolute;left:109px;top:310px;width:977px;height:1px;background:#444}
.copyright{position:absolute;left:0;width:1200px;top:322px;text-align:center;font-size:12.5px;color:#bdbdbd}
</style>
</head>
<body>

<header class="site-header">
  <div class="brand">Ridgeline<br>Build Co.</div>
  <nav class="main-nav">
    <a style="left:0">HOME</a>
    <a style="left:89px">SERVICES</a>
    <a style="left:199px">PROJECTS</a>
    <a style="left:312px">ABOUT OUR TEAM</a>
  </nav>
</header>

<section class="hero" role="img" aria-label="Photo of an engineer in a hard hat holding plans on a construction site">
  <h1 class="hero-title">RIDGELINE<br>BUILD CO.</h1>
  <p class="hero-sub">THOROUGH AND EFFECTIVE<br>CONSTRUCTION PLANS</p>
</section>

<h2 class="heading section-title" style="top:720px">Our Services</h2>

<article class="service-card" style="left:268px">
  <div class="service-icon" role="img" aria-label="Globe with location pins icon"></div>
  <h3 class="heading">Commercial Property<br>Business Owners</h3>
  <p>Lorem Ipsum is simply dummy text of the printing and typesetting industry. Lorem Ipsum has been the industry's standard dummy text ever since the 1500s, when an</p>
  <span class="btn">Learn More</span>
</article>
<article class="service-card" style="left:652px">
  <div class="service-icon" role="img" aria-label="Laptop with person icon"></div>
  <h3 class="heading">Investors of Rental<br>Properties.</h3>
  <p>Lorem Ipsum is simply dummy text of the printing and typesetting industry. Lorem Ipsum has been the industry's standard dummy text ever since the 1500s, when an unknown printer took</p>
  <span class="btn">Learn More</span>
</article>

<div class="approach-photo" role="img" aria-label="Photo of a smiling family sitting under a roof shape made by the parents' arms"></div>
<section class="approach-panel">
  <h2 class="heading">Approach Us... Ready to Help</h2>
  <p class="lead">It is a long established fact that a reader will be distracted by the readable content of a page when looking at its layout. The point of using Lorem Ipsum is that it has a more-or-less normal distribution of letters, as opposed to using 'Content here, content here', making it look like readable English. Many desktop publishing packages accident, sometimes on purpose (injected humour and the like).It is a long established fact that a reader will be distracted</p>
  <ul class="approach-list">
    <li>Lorem Ipsum is simply dummy text of the printing</li>
    <li>Lorem Ipsum has been the industry's standard dummy text</li>
    <li>The 1500s, when an unknown printer took a galley of type and</li>
    <li>scrambled it to make a type specimen book.</li>
    <li>It has survived not only five centuries</li>
  </ul>
  <div class="query-bar">Have you any Queries ? Give us a call today!
    <svg width="24" height="24" viewBox="0 0 24 24"><circle cx="12" cy="12" r="12" fill="#333"/><path d="M8 7c1 0 1.6 1.8 1.6 2.4 0 .6-.8.8-.8 1.3 0 .9 2.6 3.5 3.5 3.5.5 0 .7-.8 1.3-.8s2.4.6 2.4 1.6-1.2 1.8-2.2 1.8C10.6 16.8 7.2 13.4 7.2 10.2 7.2 8.2 7.4 7 8 7z" fill="#fff"/></svg>
  </div>
  <span class="btn">Explore More</span>
</section>

<h2 class="heading section-title" style="top:1968px">Our Projects</h2>

<section class="projects">
  <article class="project" style="left:0">
    <div class="photo" role="img" aria-label="Photo of a modern two-storey house" style="background:linear-gradient(180deg,#8a8a8a,#5a5a5a 60%,#3c3c3c)"></div>
    <h3 class="heading">House A</h3>
    <p>Lorem Ipsum is simply dummy text of the printing and typesetting</p>
    <span class="btn">Explore More</span>
  </article>
  <article class="project" style="left:323px">
    <div class="photo" role="img" aria-label="Photo of a stucco two-storey house" style="background:linear-gradient(180deg,#7a7a7a,#6a6a6a 55%,#464646)"></div>
    <h3 class="heading">House B</h3>
    <p>Lorem Ipsum is simply dummy text of the printing and typesetting industry.</p>
    <span class="btn">Explore More</span>
  </article>
  <article class="project" style="left:652px">
    <div class="photo" role="img" aria-label="Photo of a brick house with a pitched roof" style="background:linear-gradient(180deg,#909090,#4e4e4e 55%,#3a3a3a)"></div>
    <h3 class="heading">House C</h3>
    <p>Lorem Ipsum is simply dummy text of the printing and typesetting industry.</p>
    <span class="btn">Explore More</span>
  </article>
  <article class="project" style="left:981px">
    <div class="photo" role="img" aria-label="Photo of a brick house with gabled front" style="background:linear-gradient(180deg,#6e6e6e,#555 55%,#3e3e3e)"></div>
    <h3 class="heading">House D</h3>
    <p>Lorem Ipsum is simply dummy text of the printing and typesetting industry.</p>
    <span class="btn">Explore More</span>
  </article>
</section>

<h2 class="heading section-title" style="top:2605px">Our Team</h2>

<article class="team-circle team-side" style="left:151px">
  <div class="avatar" role="img" aria-label="Portrait of team member" style="background:#b9b9b9"></div>
  <h3>CLARA VOSS</h3>
  <p>Lorem ipsum dolor sit amet, con-sec-tetur adipiscing elitsed do</p>
  <svg width="38" height="38" viewBox="0 0 38 38"><circle cx="19" cy="19" r="16" fill="none" stroke="#444" stroke-width="2"/><path d="M12 16l7 7 7-7" fill="none" stroke="#444" stroke-width="2.4"/></svg>
</article>
<article class="team-circle team-mid" style="left:432px">
  <div class="avatar" role="img" aria-label="Portrait of team member" style="background:#8d8d8d"></div>
  <h3>DANIEL R. HALE</h3>
  <p>Lorem ipsum dolor sit amet, con-sec-tetur adipiscing elitsed do</p>
  <svg width="38" height="38" viewBox="0 0 38 38"><circle cx="19" cy="19" r="16" fill="none" stroke="#fff" stroke-width="2"/><path d="M12 16l7 7 7-7" fill="none" stroke="#fff" stroke-width="2.4"/></svg>
</article>
<article class="team-circle team-side" style="left:713px">
  <div class="avatar" role="img" aria-label="Portrait of team member" style="background:#bdbdbd"></div>
  <h3>NORA KESTREL</h3>
  <p>Lorem ipsum dolor sit amet, con-sec-tetur adipiscing elitsed do</p>
  <svg width="38" height="38" viewBox="0 0 38 38"><circle cx="19" cy="19" r="16" fill="none" stroke="#444" stroke-width="2"/><path d="M12 16l7 7 7-7" fill="none" stroke="#444" stroke-width="2.4"/></svg>
</article>

<footer class="site-footer">
  <div class="footer-brand">Ridgeline<br>Build Co.</div>
  <div class="footer-col" style="left:367px">
    <h4>COMPANY</h4>
    <a>HOME</a><a>SERVICES</a><a>PROJECTS</a><a>ABOUT OUR TEAM</a>
  </div>
  <div class="footer-col" style="left:539px">
    <h4>RESOURCES</h4>
    <a>SUPPORT</a><a>BLOGS</a><a>NEWS</a><a>CONTACT US</a>
  </div>
  <div class="footer-col" style="left:709px">
    <h4>LINKS</h4>
    <a>TEAM</a><a>FAQ</a><a>WHY US</a><a>TERMS OF USE</a>
  </div>
  <div class="footer-col contact-col" style="left:873px">
    <h4>CONTACT</h4>
    <div class="contact-row" style="top:32px">PHONE NUMBER<br>(555) 014-2290
      <svg width="16" height="16" viewBox="0 0 24 24"><path d="M6 2c2 0 3 3.5 3 4.5S7.6 8 7.6 9c0 1.6 5.8 7.4 7.4 7.4 1 0 1.3-1.4 2.5-1.4S22 16 22 18s-2.5 4-4.5 4C10.5 22 2 13.5 2 6.5 2 4.5 4 2 6 2z" fill="#fff"/></svg>
    </div>
    <div class="contact-row" style="top:84px">EMAIL US<br>info@ridgelinebuild.example
      <svg width="17" height="13" viewBox="0 0 24 18"><rect x="1" y="1" width="22" height="16" fill="#fff"/><path d="M1 1l11 9 11-9" fill="none" stroke="#1b1b1b" stroke-width="2"/></svg>
    </div>
    <div class="contact-row" style="top:136px">EMAIL US<br>info@ridgelinebuild.example
      <svg width="14" height="20" viewBox="0 0 14 20"><path d="M7 0C3 0 0 3 0 7c0 5 7 13 7 13s7-8 7-13c0-4-3-7-7-7z" fill="#fff"/><circle cx="7" cy="7" r="2.6" fill="#1b1b1b"/></svg>
    </div>
  </div>
  <div class="footer-rule"></div>
  <p class="copyright">© 2023 Ridgeline Build Co. All Rights Reserved</p>
</footer>

</body>
</html>
```